Business Card Design

We are a commercial real estate brokerage in San Francisco, leasing office buildings downtown.
I would like a clean, elegant look. Simple but powerful .

Industry/Entity Type

Business

Contact Information for Business Card

Derek Holloway
lic# 07258143
415.555.0172
derek@velt-commercial.example
velt-commercial.example

```html
<!DOCTYPE html>
<html lang="en">
<head>
<meta charset="utf-8">
<title>Velt Commercial — Business Card</title>
<link rel="stylesheet" href="https://fonts.googleapis.com/css2?family=Source+Sans+3:ital,wght@0,400;0,600;1,400&display=swap">
<style>
  :root {
    --page-bg: #d4d4d7;
    --card-bg: #ecedf1;
    --ink: #2b2b2d;
    --ink-soft: #4d4d50;
    --accent: #5f7191;
    --art-dark: #3c3c40;
    --art-light: #9ea3ad;
  }
  * { margin: 0; padding: 0; box-sizing: border-box; }
  html, body {
    width: 1105px;
    height: 1200px;
    overflow: hidden;
    background: var(--page-bg);
    font-family: "Source Sans 3", sans-serif;
  }
  .card {
    position: absolute;
    left: 180px;
    width: 744px;
    height: 426px;
    background: var(--card-bg);
  }
  .card--front { top: 119px; }
  .card--back { top: 635px; }

  /* Front */
  .skyline-art {
    position: absolute;
    left: 241px;
    top: 69px;
    width: 261px;
    height: 178px;
    background: linear-gradient(180deg, var(--art-light) 0%, var(--art-dark) 100%);
  }
  .ground-line {
    position: absolute;
    left: 98px;
    top: 245px;
    width: 546px;
    height: 4px;
    background: var(--ink);
  }
  .identity {
    position: absolute;
    right: calc(744px - 290px);
    top: 306px;
    text-align: right;
  }
  .identity__name {
    font-size: 26px;
    font-weight: 600;
    color: var(--accent);
    line-height: 1.2;
  }
  .identity__license {
    font-size: 19px;
    color: var(--ink-soft);
    margin-top: 4px;
  }
  .contact-list {
    position: absolute;
    left: 326px;
    top: 283px;
    list-style: none;
  }
  .contact-list__item {
    display: flex;
    align-items: center;
    height: 29px;
    font-size: 19px;
    color: var(--ink-soft);
  }
  .contact-list__icon {
    width: 18px;
    height: 18px;
    margin-right: 10px;
    fill: var(--accent);
  }

  /* Back */
  .brand {
    position: absolute;
    left: 0;
    right: 0;
    top: 178px;
    display: flex;
    justify-content: center;
    align-items: center;
    gap: 18px;
  }
  .brand__mark {
    width: 34px;
    height: 34px;
    background: var(--art-dark);
  }
  .brand__name {
    font-size: 50px;
    font-weight: 600;
    letter-spacing: 1px;
    color: var(--accent);
    line-height: 1;
  }
  .tagline {
    position: absolute;
    left: 0;
    right: 0;
    top: 317px;
    text-align: center;
    font-size: 19px;
    font-style: italic;
    line-height: 28px;
    color: var(--ink-soft);
  }
</style>
</head>
<body>
  <section class="card card--front">
    <div class="skyline-art" role="img" aria-label="City skyline illustration of downtown office towers"></div>
    <div class="ground-line"></div>

    <div class="identity">
      <p class="identity__name">Derek Holloway</p>
      <p class="identity__license">lic# 07258143</p>
    </div>

    <ul class="contact-list">
      <li class="contact-list__item">
        <svg class="contact-list__icon" viewBox="0 0 24 24" aria-hidden="true"><path d="M6.6 10.8a15.1 15.1 0 0 0 6.6 6.6l2.2-2.2a1 1 0 0 1 1-.25 11.4 11.4 0 0 0 3.6.57 1 1 0 0 1 1 1V20a1 1 0 0 1-1 1A17 17 0 0 1 3 4a1 1 0 0 1 1-1h3.5a1 1 0 0 1 1 1c0 1.25.2 2.45.57 3.57a1 1 0 0 1-.25 1z"/></svg>
        415.555.0172
      </li>
      <li class="contact-list__item">
        <svg class="contact-list__icon" viewBox="0 0 24 24" aria-hidden="true"><path d="M3 5h18v14H3z M4.5 6.5v.6l7.5 5.2 7.5-5.2v-.6z" fill-rule="evenodd"/></svg>
        derek@velt-commercial.example
      </li>
      <li class="contact-list__item">
        <svg class="contact-list__icon" viewBox="0 0 24 24" aria-hidden="true"><circle cx="12" cy="12" r="10"/><path d="M2 12h20M12 2c3 3 3 17 0 20M12 2c-3 3-3 17 0 20" stroke="#ecedf1" stroke-width="1.4" fill="none"/></svg>
        velt-commercial.example
      </li>
    </ul>
  </section>

  <section class="card card--back">
    <div class="brand">
      <span class="brand__mark" aria-hidden="true"></span>
      <h1 class="brand__name">VELT COMMERCIAL</h1>
    </div>
    <p class="tagline">commercial real estate brokerage in San Francisco<br>leasing office buildings downtown.</p>
  </section>
</body>
</html>
```